Dalvick's Business Card

I need some designs for a new business card including the new logo attached. An old example of our business card is also attached to show all the data that should be included on the new design.
**I added some more examples someone had mocked up**

Contact Information for Business Card

Should include all info on other examples uploaded.

```html
<!DOCTYPE html>
<html lang="en">
<head>
<meta charset="utf-8">
<title>Dalvick's Business Card</title>
<link href="https://fonts.googleapis.com/css2?family=Montserrat:wght@400;500;600;700&display=swap" rel="stylesheet">
<style>
  :root {
    --backdrop: #8d7150;
    --card: #232324;
    --blue: #1b72bb;
    --red: #e02327;
    --white: #ffffff;
  }
  html, body {
    margin: 0;
    padding: 0;
    width: 900px;
    height: 1200px;
    overflow: hidden;
    background: var(--backdrop);
    font-family: "Montserrat", Arial, sans-serif;
  }
  .card {
    position: absolute;
    left: 78px;
    width: 744px;
    height: 442px;
    border-radius: 30px;
    background: var(--card);
    overflow: hidden;
    box-shadow: 0 6px 14px rgba(0,0,0,0.45);
  }
  .card--front { top: 130px; }
  .card--back { top: 638px; }

  .brand { position: absolute; }
  .brand__mark {
    position: absolute;
    width: 110px;
    height: 110px;
    border-radius: 50%;
    background: var(--blue);
  }
  .brand__name {
    position: absolute;
    margin: 0;
    color: var(--blue);
    font-weight: 600;
    letter-spacing: 1px;
    line-height: 1;
    white-space: nowrap;
  }
  .brand__tagline {
    position: absolute;
    margin: 0;
    color: var(--red);
    font-weight: 700;
    white-space: nowrap;
    line-height: 1;
  }

  .card--front .brand__mark { left: 95px; top: 115px; }
  .card--front .brand__name { left: 227px; top: 126px; font-size: 66px; }
  .card--front .brand__tagline { left: 228px; top: 199px; font-size: 18.5px; }

  .card--back .brand__mark { left: 90px; top: 170px; }
  .card--back .brand__name { left: 220px; top: 180px; font-size: 71px; }
  .card--back .brand__tagline { left: 221px; top: 258px; font-size: 19.5px; }

  .person {
    position: absolute;
    right: 392px;
    top: 316px;
    margin: 0;
    color: var(--blue);
    font-size: 26px;
    font-weight: 700;
    white-space: nowrap;
  }
  .divider {
    position: absolute;
    left: 374px;
    top: 309px;
    width: 1.5px;
    height: 40px;
    background: var(--blue);
  }
  .contact {
    position: absolute;
    left: 400px;
    top: 304px;
    margin: 0;
    padding: 0;
    list-style: none;
    color: var(--white);
    font-size: 17px;
    font-weight: 400;
  }
  .contact li {
    display: flex;
    align-items: center;
    height: 23px;
  }
  .contact svg { width: 14px; height: 12px; margin-right: 10px; }

  .bands {
    position: absolute;
    left: 0;
    top: 400px;
    width: 744px;
    height: 42px;
  }
  .band-label {
    position: absolute;
    top: 413px;
    margin: 0;
    color: var(--white);
    font-size: 16px;
    font-weight: 500;
    white-space: nowrap;
    transform: translateX(-50%);
  }
  .band-label--blue { left: 190px; }
  .band-label--red { left: 556px; top: 411px; }

  .base-line {
    position: absolute;
    left: 0;
    bottom: 4px;
    width: 744px;
    height: 7px;
    background: var(--red);
  }
</style>
</head>
<body>

<section class="card card--front">
  <div class="brand">
    <div class="brand__mark"></div>
    <h1 class="brand__name">DALVICK'S</h1>
    <p class="brand__tagline">AIR CONDITIONING &amp; HEATING SERVICE</p>
  </div>

  <p class="person">Mark Dalvick</p>
  <div class="divider"></div>
  <ul class="contact">
    <li>
      <svg viewBox="0 0 14 12" aria-hidden="true"><path d="M1 4 Q7 0 13 4 L11 5.5 L9 4.5 L9 3.5 Q7 3 5 3.5 L5 4.5 L3 5.5 Z M3 7 H11 L12 11.5 H2 Z" fill="#e02327"/></svg>
      555.014.2290
    </li>
    <li>
      <svg viewBox="0 0 14 12" aria-hidden="true"><rect x="1" y="2" width="12" height="9" fill="#1b72bb"/><path d="M1 2 L7 7 L13 2" stroke="#232324" stroke-width="1.3" fill="none"/></svg>
      hvacdalvick@mailbox.com
    </li>
  </ul>

  <svg class="bands" viewBox="0 0 744 42" aria-hidden="true">
    <polygon points="0,0 394,0 374,42 0,42" fill="#1b72bb"/>
    <polygon points="400,0 744,0 744,42 380,42" fill="#e02327"/>
  </svg>
  <p class="band-label band-label--blue">LICENSED &amp; INSURED</p>
  <p class="band-label band-label--red">FAMILY OWNED &amp; OPERATED</p>
</section>

<section class="card card--back">
  <div class="brand">
    <div class="brand__mark"></div>
    <h2 class="brand__name">DALVICK'S</h2>
    <p class="brand__tagline">AIR CONDITIONING &amp; HEATING SERVICE</p>
  </div>
  <div class="base-line"></div>
</section>

</body>
</html>
```